Beef cattle farm needs signs which can be seen from roadside

We would like submissions of artwork for a sign that will hang from a fence or gate and will be seen by passing cars.

Existing logo and branding theme for the company is attached.

Signage can be between 900mm x 400mm - 1200mm x 600mm

Industry/Entity Type

Farm

Requirements
Must have
• the Signs should have the following information:
• Company name: Wendlow Grazing Company
• Address: 417 Corrigan Flat Road
• Contact number: 0431 862 407
• email address: admin@wendlowgrazingcompany.com.au
• - Logo and branding as per attached artwork

```html
<!DOCTYPE html>
<html lang="en">
<head>
<meta charset="utf-8">
<title>Wendlow Grazing Company – Roadside Sign</title>
<link href="https://fonts.googleapis.com/css2?family=Montserrat:wght@500&family=Arimo:wght@400;700&display=swap" rel="stylesheet">
<style>
  :root {
    --backdrop: #b9b6b6;
    --sign-white: #ffffff;
    --farm-green: #155c37;
    --slate-grey: #6d6e71;
    --ridge-grey: #a3a4a6;
    --cattle-grey: #9d9ea0;
    --text-white: #ffffff;
  }
  * { margin: 0; padding: 0; box-sizing: border-box; }
  html, body {
    width: 1200px;
    height: 655px;
    overflow: hidden;
    background: var(--backdrop);
  }
  .sign {
    position: absolute;
    left: 109px;
    top: 108px;
    width: 982px;
    height: 437px;
    background: var(--sign-white);
    overflow: hidden;
  }
  .landscape {
    position: absolute;
    inset: 0;
    width: 982px;
    height: 437px;
  }
  .brand-disc {
    position: absolute;
    left: 68px;
    top: 24px;
    width: 266px;
    height: 266px;
    border-radius: 50%;
    background: var(--farm-green);
  }
  .brand-name {
    position: absolute;
    left: 376px;
    top: 66px;
    width: 540px;
    font-family: "Montserrat", sans-serif;
    font-weight: 500;
    line-height: 1;
    white-space: nowrap;
  }
  .brand-name .name-main {
    display: block;
    color: var(--farm-green);
    font-size: 84px;
    letter-spacing: 0;
  }
  .brand-name .name-sub {
    display: block;
    margin-top: 24px;
    color: var(--slate-grey);
    font-size: 44px;
    letter-spacing: 1.5px;
  }
  .cattle {
    position: absolute;
    background: var(--cattle-grey);
    border-radius: 6px 10px 4px 4px;
  }
  .contact {
    position: absolute;
    right: 48px;
    top: 306px;
    text-align: right;
    color: var(--text-white);
    font-family: "Arimo", Arial, sans-serif;
  }
  .contact .phone {
    font-weight: 700;
    font-size: 33px;
    line-height: 40px;
  }
  .contact .address {
    margin-top: 6px;
    font-size: 21px;
    line-height: 26px;
  }
  .contact .email {
    margin-top: 10px;
    font-size: 20px;
    line-height: 26px;
  }
  .contact .icon {
    display: inline-block;
    vertical-align: -2px;
    margin-right: 8px;
  }
</style>
</head>
<body>
  <div class="sign">
    <svg class="landscape" viewBox="0 0 982 437" aria-hidden="true">
      <path d="M0,296 C70,335 150,348 230,340 C430,318 700,250 982,258 L982,437 L0,437 Z" fill="var(--ridge-grey)"/>
      <path d="M0,312 C70,348 150,358 230,350 C430,328 700,264 982,274 L982,437 L0,437 Z" fill="var(--farm-green)"/>
    </svg>

    <div class="brand-disc" aria-hidden="true"></div>
    <h1 class="brand-name">
      <span class="name-main">WENDLOW</span>
      <span class="name-sub">GRAZING COMPANY</span>
    </h1>

    <div class="cattle" role="img" aria-label="Silhouette of a grazing cow" style="left:124px;top:318px;width:35px;height:34px"></div>
    <div class="cattle" role="img" aria-label="Silhouette of a grazing cow" style="left:173px;top:320px;width:55px;height:34px"></div>
    <div class="cattle" role="img" aria-label="Silhouette of a cow on the ridge" style="left:394px;top:281px;width:60px;height:39px"></div>
    <div class="cattle" role="img" aria-label="Silhouette of a cow on the ridge" style="left:483px;top:271px;width:43px;height:31px"></div>
    <div class="cattle" role="img" aria-label="Silhouette of a grazing cow" style="left:577px;top:243px;width:54px;height:37px"></div>
    <div class="cattle" role="img" aria-label="Silhouette of a distant grazing cow" style="left:914px;top:228px;width:27px;height:28px"></div>

    <div class="contact">
      <p class="phone">Call : 0431 862 407</p>
      <p class="address"><svg class="icon" width="14" height="19" viewBox="0 0 14 19" aria-hidden="true"><path d="M7,0 C3.1,0 0,3.1 0,7 C0,12 7,19 7,19 C7,19 14,12 14,7 C14,3.1 10.9,0 7,0 Z M7,9.8 A2.8,2.8 0 1 1 7,4.2 A2.8,2.8 0 1 1 7,9.8 Z" fill="var(--text-white)"/></svg>417 Corrigan Flat Road</p>
      <p class="email"><svg class="icon" width="22" height="15" viewBox="0 0 22 15" aria-hidden="true"><rect x="0" y="0" width="22" height="15" fill="var(--text-white)"/><path d="M0.8,0.8 L11,8.5 L21.2,0.8" fill="none" stroke="var(--farm-green)" stroke-width="1.4"/></svg>admin@wendlowgrazingcompany.com.au</p>
    </div>
  </div>
</body>
</html>
```